Need help in designing new business card utilizing our new logo.

BuildMark Solutions works with Construction Business Owners, Managers & IT Professionals to strengthen software usage and increase user productivity.

Our Construction Accounting and Mobile Field Management Software Clients engage with us in the following areas:

New Software Implementations
Software Re-Implementations
Redesigning Software Usage at the User Level
Project Coordination & Management
Continued Software Support

Old tag line:
Planning Ahead - Delivering Results

www.buildmark-solutions.example

Ridge 4 is a product, but not needed for a new business card.

```html
<!DOCTYPE html>
<html lang="en">
<head>
<meta charset="utf-8">
<title>BuildMark Solutions — Business Card</title>
<link href="https://fonts.googleapis.com/css2?family=Roboto:wght@400;500;700&family=Roboto+Condensed:wght@700&display=swap" rel="stylesheet">
<style>
  :root{
    --navy:#0b1a8f;
    --ink:#2b2b2b;
    --grey:#8e8e8e;
    --card:#f1f1f2;
    --card-edge:#e4e4e6;
    --backdrop:#bdbdbd;
    --band-text:#ffffff;
  }
  *{box-sizing:border-box;margin:0;padding:0}
  html,body{width:1200px;height:576px;overflow:hidden}
  body{background:var(--backdrop);font-family:'Roboto',sans-serif;position:relative}
  .card{
    position:absolute;top:138px;width:484px;height:294px;border-radius:14px;
    background:linear-gradient(135deg,#fafafa 0%,var(--card) 55%,var(--card-edge) 100%);
    box-shadow:0 3px 6px rgba(0,0,0,.25);overflow:hidden;
  }
  .card--front{left:82px}
  .card--back{left:602px}

  /* front */
  .brand{display:flex;align-items:center;gap:10px}
  .brand__mark{width:14px;height:14px;background:var(--navy)}
  .brand__name{color:var(--navy);font-weight:700;letter-spacing:.5px}
  .card--front .brand{position:absolute;top:60px;left:0;right:0;justify-content:center}
  .card--front .brand__name{font-size:30px}
  .services{
    position:absolute;top:168px;left:0;right:0;height:80px;background:var(--navy);
    color:var(--band-text);font-size:13px;line-height:18.5px;text-align:center;
    display:flex;flex-direction:column;justify-content:center;
  }
  .services .sep{margin:0 9px}
  .front-web{
    position:absolute;top:262px;left:0;right:0;display:flex;justify-content:center;align-items:center;gap:18px;
    color:var(--navy);font-size:12px;
  }
  .rule{display:block;width:38px;height:2px;background:linear-gradient(90deg,transparent,#9a9a9a,transparent)}

  /* back */
  .card--back .brand{position:absolute;top:114px;left:22px}
  .card--back .brand__mark{width:10px;height:10px}
  .card--back .brand__name{font-size:17px}
  .tagline{position:absolute;top:142px;left:42px;color:var(--grey);font-size:7px}
  .person{position:absolute;top:74px;left:254px}
  .person__name{font-family:'Roboto Condensed',sans-serif;font-weight:700;font-size:20px;color:var(--navy)}
  .person__role{font-size:11px;color:var(--ink);margin-top:2px}
  .contacts{position:absolute;top:127px;left:254px;list-style:none;font-size:11px;color:var(--ink)}
  .contacts li{display:flex;align-items:center;gap:9px;height:16.5px}
  .contacts svg{width:11px;height:11px;fill:var(--navy);flex:none}
  .address{
    position:absolute;top:264px;left:0;right:0;display:flex;justify-content:center;align-items:center;gap:26px;
    font-size:11.5px;color:var(--ink);
  }
  .address .rule{background:linear-gradient(90deg,transparent,var(--navy) 40%,var(--navy) 60%,transparent);width:36px}
</style>
</head>
<body>
  <section class="card card--front" aria-label="Card front">
    <div class="brand">
      <span class="brand__mark"></span>
      <span class="brand__name">BuildMark Solutions</span>
    </div>
    <div class="services">
      <p>New Software Implementations<span class="sep">|</span>Software Re-Implementations</p>
      <p>Redesigning Software Usage at the User Level</p>
      <p>Project Coordination &amp; Management<span class="sep">|</span>Continued Software Support</p>
    </div>
    <div class="front-web">
      <span class="rule"></span>
      <span>www.buildmark-solutions.example</span>
      <span class="rule"></span>
    </div>
  </section>

  <section class="card card--back" aria-label="Card back">
    <div class="brand">
      <span class="brand__mark"></span>
      <span class="brand__name">BuildMark Solutions</span>
    </div>
    <p class="tagline">Planning Ahead - Delivering Results</p>

    <div class="person">
      <h1 class="person__name">Dana J. Hale</h1>
      <p class="person__role">Owner</p>
    </div>

    <ul class="contacts">
      <li><svg viewBox="0 0 12 12" aria-hidden="true"><path d="M3 0h6a1 1 0 0 1 1 1v10a1 1 0 0 1-1 1H3a1 1 0 0 1-1-1V1a1 1 0 0 1 1-1zm0 1.5v8h6v-8z"/></svg>555-014-7721</li>
      <li><svg viewBox="0 0 12 12" aria-hidden="true"><path d="M0 4c0-1.5 2.5-3 6-3s6 1.5 6 3v1H9V3.8H3V5H0zM2 6h8l1 5H1z"/></svg>800-555-0142 ext. 100</li>
      <li><svg viewBox="0 0 12 12" aria-hidden="true"><path d="M0 2h12v8H0zm1 1v.4l5 3.2 5-3.2V3z"/></svg>dana.hale@buildmark-solutions.example</li>
      <li><svg viewBox="0 0 12 12" aria-hidden="true"><path d="M6 0a6 6 0 1 0 0 12A6 6 0 0 0 6 0zm-1 1.2C4 2.5 3.6 4 3.5 5.5H1.1A5 5 0 0 1 5 1.2zm2 0a5 5 0 0 1 3.9 4.3H8.5C8.4 4 8 2.5 7 1.2zM4.5 5.5C4.6 4 5 2.6 6 1.4c1 1.2 1.4 2.6 1.5 4.1zm-3.4 1h2.4c.1 1.5.5 3 1.5 4.3A5 5 0 0 1 1.1 6.5zm3.4 0h3c-.1 1.5-.5 2.9-1.5 4.1-1-1.2-1.4-2.6-1.5-4.1zm4 0h2.4A5 5 0 0 1 7 10.8c1-1.3 1.4-2.8 1.5-4.3z"/></svg>www.buildmark-solutions.example</li>
    </ul>

    <div class="address">
      <span class="rule"></span>
      <span>14 Mercer Lane - Suite 210 Hudson Falls, NY 12839</span>
      <span class="rule"></span>
    </div>
  </section>
</body>
</html>
```